New Website Design for PHOVAN.org

We are looking for a new website design for PHOVAN.org. PHOVAN is a non profit home inspector association based in California. Home Inspectors are people that come out and look at a house before it's purchased to let the buyer know of any defects that may exist.
Our site is based on Joomla so if you'll be able to make a Joomla 3 template as well, please let us know (not required, but a bonus).
We would like to see designs that incorporate royal blue, white and chrome into the site as that's our main business colors.
We would like a place for rotating banners though they don't need to be the same size as the current site.
We would like navigation to be easier to manage with menus only across the top (via drop down menus) where we are going to sort out the items currently on the side. Possibly the front page could have a graphic link to separate portals for Realtors, Home Buyers and Inspectors, but that's just one option.
We would like a good mobile design or something that will scale easily to mobile.
The Find an Inspector feature is important and should stand out. The ASK PHOVANr site
Current home page feels a bit busy. Would like to simplify a bit.

```html
<!DOCTYPE html>
<html lang="en">
<head>
<meta charset="utf-8">
<title>PHOVAN – Home Inspection Association</title>
<link rel="stylesheet" href="https://fonts.googleapis.com/css2?family=Istok+Web:ital,wght@0,400;0,700;1,700&family=Ubuntu:wght@300;400&display=swap">
<style>
:root{
  --royal:#243d8f;
  --royal-dark:#1a2f73;
  --royal-light:#3c59b5;
  --ink:#2b2b2b;
  --muted:#8a8a8a;
  --link:#3f86c8;
  --chrome-top:#fbfbfb;
  --chrome-bottom:#e4e4e4;
  --paper:#f6f5f1;
  --black:#0d0d0d;
}
*{box-sizing:border-box;margin:0;padding:0}
html,body{width:1029px;height:1200px;overflow:hidden;background:#fff}
body{font-family:"Istok Web",Arial,sans-serif;color:var(--ink)}
.page{width:1200px;height:1400px;transform:scale(0.8575);transform-origin:0 0;position:relative;background:#fff}
.wrap{width:955px;margin:0 auto;position:relative}

/* header */
.site-header{height:136px;background:repeating-linear-gradient(135deg,#f7f7f7 0 2px,#f1f1f1 2px 4px)}
.brand{position:absolute;left:0;top:20px;display:flex;align-items:center;gap:18px}
.brand-dot{width:100px;height:100px;border-radius:50%;background:var(--royal)}
.brand-name{font-size:24px;line-height:29px;color:#222;font-weight:400}
.account{position:absolute;right:8px;top:0;background:var(--royal);color:#fff;font-size:11px;letter-spacing:.5px;padding:9px 13px 7px;border-radius:0 0 4px 4px;box-shadow:inset 0 -2px 0 var(--royal-dark)}
.account span{margin:0 10px;opacity:.7}
.support{position:absolute;right:0;top:58px;display:flex;align-items:center;gap:10px}
.support-text{font-family:Ubuntu,sans-serif;text-align:left}
.support-text small{display:block;color:var(--royal);font-size:15px}
.support-text strong{display:block;font-weight:300;font-size:24px;color:#222;line-height:26px}

/* nav */
.main-nav{height:50px;background:linear-gradient(var(--chrome-top),var(--chrome-bottom));border-top:1px solid #ddd;border-bottom:1px solid #d2d2d2}
.main-nav ul{list-style:none;display:flex;justify-content:space-between;align-items:center;height:48px}
.main-nav li{font-size:15px;color:#222}
.main-nav li.active{background:linear-gradient(var(--royal-light),var(--royal-dark));color:#fff;padding:7px 18px;border-radius:4px;border:1px solid var(--royal-dark)}

/* hero */
.hero{height:405px;position:relative;background:linear-gradient(100deg,#d9d6d0 0%,#c9c2b6 20%,#8b5f3c 42%,#5a3a22 60%,#2a1a10 80%,#1b120c 100%)}
.hero-copy{position:absolute;left:644px;top:205px;color:#fff}
.hero-copy .kicker{font-size:36px;font-weight:400;line-height:40px}
.hero-copy h1{font-size:42px;font-weight:400;line-height:52px;margin-bottom:10px}
.hero-copy p{font-size:15px;line-height:19px}

/* cta */
.cta{height:90px;background:linear-gradient(#f9f9f9,#e8e8e8);border-bottom:1px solid #ddd}
.cta p{position:absolute;left:0;top:20px;width:730px;font-size:17px;line-height:26px;color:#333}
.find-btn{position:absolute;right:0;top:13px;width:176px;height:58px;border-radius:29px;background:linear-gradient(var(--royal-light),var(--royal-dark));color:#fff;font-size:16px;letter-spacing:.5px;display:flex;align-items:center;justify-content:center;box-shadow:0 4px 4px rgba(0,0,0,.2)}

/* portals */
.portals{height:227px;background:var(--paper)}
.portal{position:absolute;top:28px;width:270px}
.portal-head{display:flex;align-items:center;gap:15px;margin-bottom:30px}
.portal-icon{width:67px;height:67px;border-radius:50%;background:var(--royal);display:flex;align-items:center;justify-content:center;box-shadow:inset 0 0 0 3px var(--royal-dark)}
.portal h2{font-size:25px;font-weight:400;line-height:24px;color:#333}
.portal p{font-size:13px;line-height:20.5px;color:var(--muted)}
.portal a{color:var(--link);text-decoration:none}

/* welcome */
.welcome{height:222px;border-top:1px solid #e6e6e6}
.welcome h2{position:absolute;left:0;top:28px;font-size:24px;font-weight:400;color:#333}
.welcome .copy{position:absolute;left:0;top:72px;width:672px;font-size:12.5px;line-height:18px;color:var(--muted)}
.welcome .copy p+p{margin-top:10px}
.welcome figure{position:absolute;right:0;top:25px;width:258px;height:158px;border:1px solid #e2e2e2;background:#fff;padding:10px}
.photo-ladder{width:100%;height:100%;background:linear-gradient(110deg,#d8d2bb 0%,#c9c2a6 35%,#5a83c9 55%,#1f57b8 100%)}

/* footer */
.site-footer{height:230px;background:var(--royal);border-top:2px solid #111;color:#fff}
.col{position:absolute;top:30px}
.col h3{font-size:20px;font-weight:400;letter-spacing:.5px;margin-bottom:18px}
.col p,.col li{font-size:13px;line-height:17px}
.col ul{list-style:none}
.col li{margin-bottom:5px}
.col .who{font-weight:700;font-style:italic;margin:4px 0 16px}
.field{width:186px;height:28px;border-radius:4px;background:linear-gradient(#fff,#e6e6e6);color:#888;font-size:12px;padding:6px 8px;margin-bottom:10px}
.login-btn{display:inline-block;background:linear-gradient(#fff,#e1e1e1);color:#333;font-size:13px;padding:3px 15px;border-radius:3px;margin-top:6px}

.bottom-bar{height:42px;background:var(--black);color:#fff;font-size:13px}
.bottom-bar .copy{position:absolute;left:0;top:12px}
.bottom-bar ul{position:absolute;right:0;top:11px;list-style:none;display:flex;gap:30px}
</style>
</head>
<body>
<div class="page">

  <header class="site-header">
    <div class="wrap">
      <div class="brand">
        <div class="brand-dot"></div>
        <div class="brand-name">PHOVAN Home Inspectors<br>Association</div>
      </div>
      <div class="account">SIGN UP<span>|</span>LOGIN</div>
      <div class="support">
        <svg width="46" height="48" viewBox="0 0 46 48" aria-hidden="true">
          <path d="M8 26 A15 15 0 0 1 38 26" fill="none" stroke="#333" stroke-width="4"/>
          <rect x="3" y="24" width="10" height="16" rx="4" fill="#333"/>
          <rect x="33" y="24" width="10" height="16" rx="4" fill="#333"/>
          <path d="M38 38 Q36 46 26 45" fill="none" stroke="#333" stroke-width="2"/>
        </svg>
        <div class="support-text"><small>24/7 Online Support</small><strong>1-300-555-0142</strong></div>
      </div>
    </div>
  </header>

  <nav class="main-nav">
    <ul class="wrap" style="width:968px">
      <li class="active">Home</li>
      <li>Find an Inspector</li>
      <li>Home Buyers &amp; Sellers</li>
      <li>Real Estate Agents</li>
      <li>Inspectors</li>
      <li>Ask PHOVAN</li>
      <li>Conferences</li>
    </ul>
  </nav>

  <section class="hero" role="img" aria-label="Home inspector in a white hard hat shining a red flashlight along a basement beam">
    <div class="hero-copy">
      <div class="kicker">The Leader in</div>
      <h1>Home Inspection Service</h1>
      <p>Le Lorem Ipsum est simplement du faux texte employé<br>dans la composition et la mise en page avant impression.<br>Le Lorem Ipsum est le faux.</p>
    </div>
  </section>

  <section class="cta">
    <div class="wrap">
      <p>Le Lorem Ipsum est simplement du faux texte employé dans la composition et la mise en page avant impression.</p>
      <div class="find-btn">FIND INSPECTOR</div>
    </div>
  </section>

  <section class="portals">
    <div class="wrap">
      <div class="portal" style="left:18px">
        <div class="portal-head">
          <div class="portal-icon"><svg width="36" height="34" viewBox="0 0 36 34"><path d="M4 16 L18 4 L32 16 M8 14 V30 H28 V14" fill="none" stroke="#fff" stroke-width="3"/><circle cx="15" cy="22" r="3" fill="#fff"/><path d="M17 22 H25 V25" stroke="#fff" stroke-width="2" fill="none"/></svg></div>
          <h2>Home<br>Buyers</h2>
        </div>
        <p>Le Lorem Ipsum est simplement du faux texte employé dans la composition et la mise en page avant impression. Le Lorem Ipsum est le faux texte standard. <a>More Info</a></p>
      </div>
      <div class="portal" style="left:344px">
        <div class="portal-head">
          <div class="portal-icon"><svg width="36" height="34" viewBox="0 0 36 34"><path d="M4 16 L18 4 L32 16 M8 14 V30 H28 V14" fill="none" stroke="#fff" stroke-width="3"/><circle cx="16" cy="21" r="4" fill="none" stroke="#fff" stroke-width="2"/><path d="M19 24 L24 29" stroke="#fff" stroke-width="2.5"/></svg></div>
          <h2>Home<br>Inspectors</h2>
        </div>
        <p>Le Lorem Ipsum est simplement du faux texte employé dans la composition et la mise en page avant impression. Le Lorem Ipsum est le faux texte standard. <a>More Info</a></p>
      </div>
      <div class="portal" style="left:672px">
        <div class="portal-head">
          <div class="portal-icon"><svg width="36" height="34" viewBox="0 0 36 34"><path d="M4 16 L18 4 L32 16 M8 14 V30 H28 V14" fill="none" stroke="#fff" stroke-width="3"/><rect x="11" y="18" width="14" height="9" fill="none" stroke="#fff" stroke-width="2"/><circle cx="18" cy="22.5" r="2" fill="#fff"/></svg></div>
          <h2>Home<br>Realtors</h2>
        </div>
        <p>Le Lorem Ipsum est simplement du faux texte employé dans la composition et la mise en page avant impression. Le Lorem Ipsum est le faux texte standard. <a>More Info</a></p>
      </div>
    </div>
  </section>

  <section class="welcome">
    <div class="wrap">
      <h2>Welcome to PHOVAN Home Inspectors Association</h2>
      <div class="copy">
        <p>Lorem ipsum dolor sit amet, consectetuer adipiscing elit, sed diam nonummy nibh euismod tincidunt ut laoreet dolore magna aliquam erat volutpat. Ut wisi enim ad minim veniam, quis nostrud exerci tation ullamcorper suscipit lobortis nisl ut aliquip ex ea commodo consequat.</p>
        <p>Duis autem vel eum iriure dolor in hendrerit in vulputate velit esse molestie consequat, vel illum dolore eu feugiat nulla facilisis at vero eros et accumsan et iusto odio dignissim qui blandit praesent luptatum zzril delenit augue duis dolore te feugait nulla facilisi. Nam liber tempor cum.</p>
      </div>
      <figure><div class="photo-ladder" role="img" aria-label="Inspector climbing a ladder against a house under a blue sky"></div></figure>
    </div>
  </section>

  <footer class="site-footer">
    <div class="wrap">
      <div class="col" style="left:3px">
        <h3>Contact Details</h3>
        <p>1264 Some Building, Street<br>City, Postal Code</p>
        <p style="margin-top:17px">Phone No. : 00 123 254-1234</p>
        <p style="margin-top:17px">E-mail : support@phovan.org</p>
      </div>
      <div class="col" style="left:268px">
        <h3>SiteMap</h3>
        <ul>
          <li>Lorem Ipsum is simplement</li>
          <li>Dignissim qui blandit praesent</li>
          <li>Eleend oon congue imperdie</li>
          <li>Claritas process dynamicus</li>
          <li>Laoreet dolore magna aliquam</li>
        </ul>
      </div>
      <div class="col" style="left:508px">
        <h3>Testimonials</h3>
        <p>Lorem Ipsum est simplement du<br>fauxtexte employé.</p>
        <p class="who">Marlow Jennings</p>
        <p>Lorem Ipsum est simplement du<br>fauxtexte employé.</p>
        <p class="who">Anonymous</p>
      </div>
      <div class="col" style="left:767px">
        <h3>Inspector Login</h3>
        <div class="field">username</div>
        <div class="field">password</div>
        <p style="margin-left:8px">Forgot your password</p>
        <span class="login-btn">Log in</span>
      </div>
    </div>
  </footer>

  <div class="bottom-bar">
    <div class="wrap">
      <span class="copy">Copyright 2012. Company Name, All Rights Reserved.</span>
      <ul><li>Home</li><li>Find an Inspector</li><li>Ask PHOVAN</li><li>Conferences</li></ul>
    </div>
  </div>

</div>
</body>
</html>
```